A start-up named "lumerova" - a clinical research organization needs a new PowerPoint design

We need a new PowerPoint Design (incl. business card and stationery design) for an early-stage start-up named "lumerova" seeking to build an ecosystem/ strategic partner alliances or consortium of committed and active collaborators to guide important components of the clinical trial.

Our ultimate goal is to avoid false neutrals – therapies that have not been and may never be evaluated in clinical trials due to the costs and/ or complexity.

The final design should highlight our patient-centric approach, innovative study design supported with the novel AI platform to make a stronger impact on patient lives.

Please see the attached brief for more details.
Updates

Requesting the proposals on color-coding, business-card designs, clinical research visuals, and icons as well as stationery design.

Target Market(s)

Pharma/ Biotech Executives
Medical Institutions
Clinical Trial Participants (Patients)

Colors
e34398

Requirements
Must have
• Use the Color Version of purple/ magenta logo

```html
<!DOCTYPE html>
<html lang="en">
<head>
<meta charset="utf-8">
<title>lumerova stationery</title>
<link href="https://fonts.googleapis.com/css2?family=Source+Sans+3:wght@400;600;700&display=swap" rel="stylesheet">
<style>
  :root {
    --magenta: #c81f7b;
    --magenta-deep: #a9276b;
    --magenta-soft: #d23d8c;
    --paper: #ececec;
    --paper-shade: #e4e4e4;
    --ink: #3a3a3a;
    --ink-soft: #a5a5a5;
    --backdrop: #b8b8b8;
    --white: #ffffff;
  }
  * { box-sizing: border-box; margin: 0; padding: 0; }
  html, body { width: 1200px; height: 1035px; overflow: hidden; }
  body {
    background: var(--backdrop);
    font-family: "Source Sans 3", "Myriad Pro", sans-serif;
    color: var(--ink);
    position: relative;
  }
  .sheet, .envelope, .card { position: absolute; background: var(--paper); overflow: hidden; }

  /* ---------- letterhead ---------- */
  .sheet-under { left: 141px; top: 190px; width: 421px; height: 595px; background: var(--paper-shade); }
  .letterhead { left: 88px; top: 120px; width: 422px; height: 595px; }
  .lh-brand {
    position: absolute; left: 0; top: 0; width: 128px; height: 52px;
    background: linear-gradient(90deg, var(--magenta), var(--magenta-deep));
    clip-path: polygon(0 0, 100% 0, 91% 100%, 0 100%);
    display: flex; align-items: center; padding-left: 29px;
  }
  .wordmark { font-weight: 700; letter-spacing: -0.2px; line-height: 1; display: inline-flex; align-items: center; gap: 3px; }
  .wordmark .mark-square { display: inline-block; background: currentColor; }
  .lh-brand .wordmark { color: var(--white); font-size: 15px; }
  .lh-brand .mark-square { width: 6px; height: 6px; }
  .lh-rule { position: absolute; left: 0; top: 0; }
  .contact-row { position: absolute; display: flex; align-items: center; }
  .contact-item { display: flex; align-items: center; }
  .icon-box {
    background: var(--magenta); display: flex; align-items: center; justify-content: center; flex: none;
  }
  .icon-box svg { fill: none; stroke: var(--white); }
  .contact-text { color: #555; line-height: 1.2; }
  .lh-contacts { left: 145px; top: 17px; gap: 0; }
  .lh-contacts .contact-item { width: 82px; gap: 5px; }
  .lh-contacts .contact-item:nth-child(2) { width: 92px; }
  .lh-contacts .icon-box { width: 20px; height: 20px; }
  .lh-contacts .icon-box svg { width: 10px; height: 10px; }
  .lh-contacts .contact-text { font-size: 5px; }

  .letter-body { position: absolute; left: 39px; top: 99px; width: 345px; font-size: 8px; line-height: 10.3px; }
  .addr-line { display: block; font-size: 8px; line-height: 11px; }
  .addr-line.muted { color: var(--ink-soft); }
  .addr-block { margin-bottom: 10px; }
  .letter-para { text-align: justify; margin-top: 14px; }
  .letter-para + .letter-para { margin-top: 17px; }
  .sign-off { position: absolute; left: 39px; top: 458px; font-size: 8px; }
  .sign-off .muted { color: var(--ink-soft); margin-top: 11px; display: block; }
  .lh-pattern {
    position: absolute; left: 225px; top: 394px; width: 166px; height: 165px;
    background: radial-gradient(circle at 45% 50%, rgba(0,0,0,0.06), rgba(0,0,0,0.02) 70%, transparent 72%);
  }
  .lh-foot-left {
    position: absolute; left: 0; top: 574px; width: 66px; height: 17px;
    background: var(--magenta); clip-path: polygon(0 0, 100% 0, 85% 100%, 0 100%);
  }
  .lh-foot-square { position: absolute; left: 81px; top: 572px; width: 19px; height: 19px; background: var(--magenta); }
  .lh-foot-right {
    position: absolute; left: 120px; top: 574px; width: 302px; height: 17px;
    background: linear-gradient(90deg, var(--magenta) 0%, var(--magenta-deep) 70%, var(--magenta-soft) 100%);
    clip-path: polygon(4% 0, 100% 0, 100% 100%, 0 100%);
    color: var(--white); font-size: 5px; display: flex; align-items: center; padding-left: 72px;
  }

  /* ---------- envelopes ---------- */
  .envelope-back { left: 600px; top: 202px; width: 418px; height: 182px; }
  .env-flap { position: absolute; left: 0; top: 0; }
  .env-back-brand { position: absolute; left: 21px; top: 129px; color: var(--magenta); font-size: 9px; }
  .env-back-brand .mark-square { width: 4px; height: 4px; }
  .env-contacts { left: 203px; top: 126px; }
  .env-contacts .contact-item { gap: 4px; width: 63px; }
  .env-contacts .contact-item:nth-child(2) { width: 71px; }
  .env-contacts .icon-box { width: 15px; height: 14px; }
  .env-contacts .icon-box svg { width: 7px; height: 7px; }
  .env-contacts .contact-text { font-size: 3.5px; }

  .envelope-front {
    left: 693px; top: 415px; width: 419px; height: 181px;
    background: linear-gradient(90deg, #c41d78 0%, #c02478 55%, #a8306e 100%);
  }
  .env-front-pattern {
    position: absolute; left: 255px; top: 35px; width: 120px; height: 120px;
    background: radial-gradient(circle, rgba(150,40,95,0.55), rgba(150,40,95,0) 70%);
  }
  .env-front-brand { position: absolute; left: 169px; top: 81px; color: var(--white); font-size: 17px; }
  .env-front-brand .mark-square { width: 7px; height: 7px; }

  /* ---------- business cards ---------- */
  .card-front { left: 243px; top: 827px; width: 189px; height: 104px; }
  .card-front-brand { position: absolute; left: 59px; top: 34px; color: var(--magenta); font-size: 15px; }
  .card-front-brand .mark-square { width: 7px; height: 7px; }
  .card-front-band {
    position: absolute; left: 0; top: 85px; width: 189px; height: 13px; background: var(--magenta);
    display: flex; align-items: center; color: var(--white); font-size: 5px; padding-left: 26px; gap: 4px;
  }
  .band-slash { width: 1px; height: 13px; background: var(--white); transform: skewX(-25deg); opacity: 0.9; }
  .band-icon { width: 7px; height: 7px; fill: none; stroke: var(--white); }
  .band-gap { width: 6px; }

  .card-back { left: 483px; top: 828px; width: 190px; height: 105px; }
  .card-back-inner {
    position: absolute; left: 42.5px; top: -42.5px; width: 105px; height: 190px;
    transform: rotate(-90deg); background: var(--paper);
  }
  .cb-header { position: absolute; left: 0; top: 0; }
  .cb-brand { position: absolute; left: 16px; top: 12px; color: var(--white); font-size: 12px; }
  .cb-brand .mark-square { width: 5px; height: 5px; }
  .cb-portrait {
    position: absolute; left: 28px; top: 38px; width: 28px; height: 28px; border-radius: 50%;
    background: linear-gradient(160deg, #8a8f96, #4b5058); border: 1.5px solid var(--white);
  }
  .cb-icons { position: absolute; left: 8px; top: 112px; width: 18px; height: 78px; background: var(--magenta); }
  .cb-icons svg { position: absolute; left: 5px; width: 8px; height: 8px; fill: none; stroke: var(--white); }
  .cb-rows { position: absolute; left: 30px; top: 74px; width: 72px; font-size: 4.6px; line-height: 5.6px; color: #333; }
  .cb-row { padding: 3px 0; }
  .cb-row + .cb-row { border-top: 0.6px solid var(--magenta); }
  .cb-role { color: var(--magenta); display: block; }
</style>
</head>
<body>

<!-- letterhead stack -->
<div class="sheet sheet-under"></div>

<article class="sheet letterhead">
  <div class="lh-brand"><span class="wordmark">lumerova<span class="mark-square"></span></span></div>
  <svg class="lh-rule" width="422" height="56" viewBox="0 0 422 56">
    <polyline points="129,0 118,52 422,52" fill="none" stroke="var(--magenta)" stroke-width="1"/>
  </svg>
  <div class="contact-row lh-contacts">
    <div class="contact-item">
      <span class="icon-box"><svg viewBox="0 0 10 10" stroke-width="1"><circle cx="5" cy="5" r="4"/><path d="M1 5h8M5 1c-2 2.5-2 5.5 0 8M5 1c2 2.5 2 5.5 0 8"/></svg></span>
      <span class="contact-text">name@lumerova.ch<br>www.lumerova.ch</span>
    </div>
    <div class="contact-item">
      <span class="icon-box"><svg viewBox="0 0 10 10" stroke-width="1.2"><path d="M5 9.2S2 5.8 2 3.9a3 3 0 0 1 6 0C8 5.8 5 9.2 5 9.2z"/><circle cx="5" cy="3.9" r="0.9"/></svg></span>
      <span class="contact-text">Lumerova GmbH, Street<br>name 1, 9999 City name<br>Switzerland</span>
    </div>
    <div class="contact-item">
      <span class="icon-box"><svg viewBox="0 0 10 10" stroke-width="1.2"><path d="M2.5 1.5l1.5 0 .8 2-1 .8a5 5 0 0 0 2 2l.8-1 2 .8v1.5c0 .6-.5 1-1 1A7 7 0 0 1 1.5 2.5c0-.5.4-1 1-1z"/></svg></span>
      <span class="contact-text">+41 (0)44 210 50 00<br>+41 (0)44 210 58 17</span>
    </div>
  </div>

  <div class="letter-body">
    <div class="addr-block">
      <span class="addr-line">To :</span>
      <span class="addr-line">Lorem ipsum</span>
      <span class="addr-line muted">Lorem ipsum</span>
    </div>
    <div class="addr-block">
      <span class="addr-line">Lorem ipsum</span>
      <span class="addr-line muted">Lorem ipsum dolor</span>
      <span class="addr-line muted">sit amet</span>
    </div>
    <p class="letter-para">Lorem ipsum dolor sit amet, consectetur adipiscing elit, sed do eiusmod tempor incididunt ut labore et dolore magna aliqua. Ut enim ad minim veniam, quis nostrud exercitation ullamco laboris nisi ut aliquip ex ea commodo consequat. Duis aute irure dolor in reprehenderit in voluptate velit esse cillum dolore eu fugiat nulla pariatur. Excepteur sint occaecat cupidatat non proident, sunt in culpa qui officia deserunt mollit anim id est laborum.</p>
    <p class="letter-para">Sed ut perspiciatis unde omnis iste natus error sit voluptatem accusantium doloremque laudantium, totam rem aperiam, eaque ipsa quae ab illo inventore veritatis et quasi architecto beatae vitae dicta sunt explicabo. Nemo enim ipsam voluptatem quia voluptas sit aspernatur aut odit aut fugit, sed quia consequuntur magni dolores eos qui ratione voluptatem sequi nesciunt. Neque porro quisquam est, qui dolorem ipsum quia dolor sit amet, consectetur, adipisci velit, sed quia non numquam eius modi tempora incidunt ut labore et dolore magnam aliquam quaerat voluptatem. Ut enim ad minima veniam, quis nostrum exercitationem ullam corporis suscipit laboriosam, nisi ut aliquid ex ea commodi consequatur? Quis autem vel eum iure reprehenderit qui in ea voluptate velit esse quam nihil molestiae consequatur, vel illum qui dolorem eum fugiat quo voluptas nulla pariatur.</p>
  </div>

  <div class="lh-pattern" role="img" aria-label="Faint decorative brand pattern"></div>

  <div class="sign-off">
    <span>Lorem ipsum</span>
    <span class="muted">Lorem ipsum dolor</span>
  </div>

  <div class="lh-foot-left"></div>
  <div class="lh-foot-square"></div>
  <div class="lh-foot-right">www.lumerova.ch</div>
</article>

<!-- envelope, back -->
<section class="envelope envelope-back">
  <svg class="env-flap" width="418" height="55" viewBox="0 0 418 55">
    <path d="M0 0H418L408 45Q405 53 396 53H20Q12 53 9 45Z" fill="var(--magenta)"/>
  </svg>
  <span class="wordmark env-back-brand">lumerova<span class="mark-square"></span></span>
  <div class="contact-row env-contacts">
    <div class="contact-item">
      <span class="icon-box"><svg viewBox="0 0 10 10" stroke-width="1"><circle cx="5" cy="5" r="4"/><path d="M1 5h8M5 1c-2 2.5-2 5.5 0 8M5 1c2 2.5 2 5.5 0 8"/></svg></span>
      <span class="contact-text">name@lumerova.ch<br>www.lumerova.ch</span>
    </div>
    <div class="contact-item">
      <span class="icon-box"><svg viewBox="0 0 10 10" stroke-width="1.2"><path d="M5 9.2S2 5.8 2 3.9a3 3 0 0 1 6 0C8 5.8 5 9.2 5 9.2z"/><circle cx="5" cy="3.9" r="0.9"/></svg></span>
      <span class="contact-text">Lumerova GmbH, Street<br>name 1, 9999 City name<br>Switzerland</span>
    </div>
    <div class="contact-item">
      <span class="icon-box"><svg viewBox="0 0 10 10" stroke-width="1.2"><path d="M2.5 1.5l1.5 0 .8 2-1 .8a5 5 0 0 0 2 2l.8-1 2 .8v1.5c0 .6-.5 1-1 1A7 7 0 0 1 1.5 2.5c0-.5.4-1 1-1z"/></svg></span>
      <span class="contact-text">+41 (0)44 210 50 00<br>+41 (0)44 210 58 17</span>
    </div>
  </div>
</section>

<!-- envelope, front -->
<section class="envelope envelope-front">
  <div class="env-front-pattern" role="img" aria-label="Soft decorative brand pattern"></div>
  <span class="wordmark env-front-brand">lumerova<span class="mark-square"></span></span>
</section>

<!-- business card, front -->
<section class="card card-front">
  <span class="wordmark card-front-brand">lumerova<span class="mark-square"></span></span>
  <div class="card-front-band">
    <span class="band-slash"></span>
    <svg class="band-icon" viewBox="0 0 10 10" stroke-width="1"><circle cx="5" cy="5" r="4"/><path d="M1 5h8M5 1c-2 2.5-2 5.5 0 8M5 1c2 2.5 2 5.5 0 8"/></svg>
    <span class="band-slash"></span>
    <span>www.lumerova.ch</span>
    <span class="band-gap"></span>
    <span class="band-slash"></span>
    <svg class="band-icon" viewBox="0 0 10 10" stroke-width="1.2"><path d="M2.5 1.5l1.5 0 .8 2-1 .8a5 5 0 0 0 2 2l.8-1 2 .8v1.5c0 .6-.5 1-1 1A7 7 0 0 1 1.5 2.5c0-.5.4-1 1-1z"/></svg>
    <span class="band-slash"></span>
    <span>+41 (0)44 210 58 17</span>
  </div>
</section>

<!-- business card, back -->
<section class="card card-back">
  <div class="card-back-inner">
    <svg class="cb-header" width="105" height="110" viewBox="0 0 105 110">
      <path d="M0 0H105V36C80 44 62 62 55 80C50 92 38 104 0 110Z" fill="var(--magenta)"/>
    </svg>
    <span class="wordmark cb-brand">lumerova<span class="mark-square"></span></span>
    <div class="cb-portrait" role="img" aria-label="Portrait photo of the managing partner"></div>
    <div class="cb-icons">
      <svg style="top:6px" viewBox="0 0 10 10" stroke-width="1"><circle cx="5" cy="5" r="4"/><path d="M1 5h8M5 1c-2 2.5-2 5.5 0 8"/></svg>
      <svg style="top:26px" viewBox="0 0 10 10" stroke-width="1.2"><path d="M5 9.2S2 5.8 2 3.9a3 3 0 0 1 6 0C8 5.8 5 9.2 5 9.2z"/></svg>
      <svg style="top:46px" viewBox="0 0 10 10" stroke-width="1.2"><path d="M2.5 1.5l1.5 0 .8 2-1 .8a5 5 0 0 0 2 2l.8-1 2 .8v1.5c0 .6-.5 1-1 1A7 7 0 0 1 1.5 2.5c0-.5.4-1 1-1z"/></svg>
      <svg style="top:64px" viewBox="0 0 10 10" stroke-width="1.2"><rect x="2.5" y="1" width="5" height="8" rx="1"/></svg>
    </div>
    <div class="cb-rows">
      <div class="cb-row"><span class="cb-role">Managing partner</span>Name Surname, PhD</div>
      <div class="cb-row">name@lumerova.ch<br>www.lumerova.ch</div>
      <div class="cb-row">Lumerova GmbH, Street<br>name 1, 9999 City name<br>Switzerland</div>
      <div class="cb-row">+41 (0)44 210 50 00<br>+41 (0)44 210 58 17<br>+41 (0)79 482 36 15<br>+41 (0)44 210 50 01</div>
    </div>
  </div>
</section>

</body>
</html>
```